Flyer-Design für Karla Brettin
Zielgruppe
Ich bin psychologische Beraterin und Heilpraktikerin für Psychotherapie. Ich biete ein Coaching speziell für Mütter (meist Mütter mit neugeborenen Babys) an. Dieses Mütter-Coaching will ich bewerben. Die Flyer werden unter anderen an Ärzte und Hebammen weiter gegeben und dort in den Praxen ausliegen.
Aufgabenstellung
In meinem Logo herrschen die Farben orange und grau vor - es wäre schön, wenn sich diese Farben im Flyer wiederfinden würden - evtl. kombiniert mit mittelblau oder einem hellem grün.
Des weiteren möchte ich später Flyer im Din Lang Format (einseitig) mit anderen Angeboten erstellen. Das sollte mit dem Design dann auch möglich sein.
Der Schrifttyp soll bitte Arial sein, passend zum Logo. Ich habe bei Bildarro Fotos zu dem Thema erstanden, die ich stimmig finde. Diese Bilder sollten im Flyer genutzt werden.
Für diesen Flyer hätte ich gerne das Format: Falzblatt mit Wickelfalz - 279 x 219 mm

```html
<!DOCTYPE html>
<html lang="de">
<head>
<meta charset="utf-8">
<title>Coaching für Mütter – Falzblatt</title>
<link href="https://fonts.googleapis.com/css2?family=Arimo:wght@400;700&display=swap" rel="stylesheet">
<style>
:root{
  --orange:#e9a033;
  --grey:#8d8d8d;
  --grey-dark:#6f6f6f;
  --paper:#eeeeee;
  --paper-dark:#d9d9d9;
  --blue:#4a9dd6;
  --green:#9dc46c;
  --ink:#2f2f2f;
  --white:#ffffff;
  --stage:#e4e4e4;
}
*{box-sizing:border-box;margin:0;padding:0}
html,body{width:1200px;height:600px;overflow:hidden}
body{background:var(--stage);font-family:"Arimo",Arial,sans-serif;color:var(--ink);position:relative}
.spread{position:absolute;top:86px;width:576px;height:428px;display:flex;box-shadow:0 4px 14px rgba(0,0,0,.18)}
.spread--inside{left:14px}
.spread--outside{left:610px}
.panel{position:relative;width:192px;height:100%;overflow:hidden}
h2{font-weight:700;text-transform:uppercase;line-height:1.02}
p,li{font-size:6.3px;line-height:1.42}

/* Panel: Ihre Situation */
.situation{background:var(--orange)}
.situation .photo{height:150px;background:linear-gradient(135deg,#c9c3bf,#efeae6 55%,#b9b3ae)}
.situation h2{position:absolute;top:96px;left:14px;font-size:21px;color:#333}
.situation ul{list-style:none;padding:14px 14px 0 16px;color:var(--white)}
.situation li{margin-bottom:9px;padding-left:6px;position:relative}
.situation li::before{content:"•";position:absolute;left:0}

/* Panel: Meine Unterstützung */
.support{background:linear-gradient(90deg,var(--paper-dark),var(--paper) 25%,var(--white) 70%,var(--paper));padding:20px 14px 0 14px}
.support h2{font-size:16px;color:#333;margin-bottom:14px}
.support h3{color:var(--orange);font-size:11px;text-transform:uppercase;margin:10px 0 3px}
.support p{margin-bottom:5px}
.support .note{position:absolute;left:12px;right:12px;bottom:16px;background:var(--grey);color:var(--white);border-radius:12px;padding:7px 10px;font-size:5.2px;line-height:1.4;text-align:center}

/* Panel: Unser Weg */
.path{background:var(--grey)}
.path h2{color:var(--white);font-size:17px;padding:22px 0 0 14px}
.path .sub{color:var(--white);font-size:5.6px;text-transform:uppercase;padding:2px 14px 8px}
.step{height:39px;display:flex;align-items:center;gap:8px;padding:0 10px;color:var(--white);font-size:6.3px;line-height:1.4}
.step:nth-of-type(odd){background:var(--orange)}
.step:nth-of-type(even){background:var(--grey)}
.step svg{flex:0 0 22px;width:22px;height:22px}

/* Panel: Warum Coaching */
.why{background:var(--blue)}
.why .head{padding:18px 14px 10px;color:var(--white)}
.why h2{font-size:12.5px;margin-bottom:7px}
.why .head p{font-size:5.8px;font-weight:700}
.why .band{background:var(--green);padding:10px 14px;color:var(--white)}
.why .band h2{font-size:16px}
.why .body{padding:12px 14px;color:var(--white)}
.why .body p{font-size:5.7px;margin-bottom:9px}
.why .start{width:70px}
.why .bubble{position:absolute;right:12px;bottom:26px;width:82px;height:82px;border-radius:50%;background:var(--orange);color:var(--white);font-weight:700;font-size:8.3px;line-height:1.35;display:flex;align-items:center;justify-content:center;text-align:center;padding:8px}

/* Name line and offer heading */
.brand{font-weight:700;font-size:13px;color:var(--ink)}
.claim-line{color:var(--orange);font-weight:700;font-size:7.6px;text-transform:uppercase;margin-top:8px}

/* Panel: Angebote */
.offers{background:linear-gradient(90deg,var(--paper-dark),var(--white) 40%,var(--paper))}
.offers .top{padding:18px 14px 10px;height:62px}
.offer{padding:7px 12px 8px 34px;color:var(--white);position:relative;min-height:52px}
.offer h3{font-size:8.8px;text-transform:uppercase;margin-bottom:3px}
.offer p{font-size:5.4px;line-height:1.38}
.offer svg{position:absolute;left:8px;top:10px;width:20px;height:20px}
.offer--single{background:var(--orange)}
.offer--group{background:var(--blue)}
.offer--phone{background:var(--green)}
.contact{padding:10px 14px;font-size:5.6px;line-height:1.45}
.contact .call{color:var(--orange);font-weight:700;margin-bottom:6px}
.contact .name{color:var(--orange);font-weight:700}
.contact .role{font-weight:700;margin-bottom:4px}
.contact .phone{color:var(--orange);font-weight:700;margin-bottom:4px}

/* Panel: Titel */
.cover{background:var(--white)}
.cover .top{padding:18px 14px 8px;height:70px}
.cover .photo{height:160px;background:linear-gradient(160deg,#f2ede9,#d8cbc3 55%,#a99b93)}
.cover .claim{position:absolute;left:0;right:0;bottom:0;height:198px;background:var(--orange);color:var(--white);padding:24px 16px;font-size:15px;line-height:1.6;text-transform:uppercase}
.cover .claim b{font-weight:700}
</style>
</head>
<body>

<section class="spread spread--inside" aria-label="Innenseite">
  <div class="panel situation">
    <div class="photo" role="img" aria-label="Foto: erschöpfte Mutter mit Baby im Kinderbett"></div>
    <h2>Ihre<br>Situation</h2>
    <ul>
      <li>Haben Sie sich Ihr Mutterglück anders vorgestellt? - Sie hatten sich so auf Ihr Baby gefreut, aber die Realität ist gar nicht so, wie Sie sich das gedacht haben?</li>
      <li>Oder Sie haben bereits ein oder mehrere Kinder aber trotzdem ist jetzt alles anders?</li>
      <li>Fühlen Sie sich allein, isoliert: Ihre Kollegen und Freunde führen weiterhin Ihr früheres Leben - Sie sind aber nicht mehr mit dabei?</li>
      <li>Das Verständnis Ihrer Umgebung für Ihre neue Situation fehlt. Sogar die Partnerschaft ist plötzlich ganz anders als sie es vorher war?</li>
      <li>Sie werden nur noch als Mutter wahrgenommen - kaum mehr als die Frau und die Persönlichkeit, die Sie vorher waren und auch immer noch sind?</li>
      <li>Sie fühlen sich oft erschöpft, ratlos, überfordert, unverstanden?</li>
    </ul>
  </div>

  <div class="panel support">
    <h2>Meine<br>Unterstützung</h2>
    <h3>Begleitung</h3>
    <p>Die gute Nachricht: Sie müssen diese belastende Situation nicht allein bewältigen - erleben Sie Erleichterung, indem Sie sich von mir beraten lassen.</p>
    <p>Als Coach gehe ich ganz individuell auf Ihre Person und auf Ihre persönliche Situation ein.</p>
    <h3>Stärkung</h3>
    <p>Entscheiden Sie sich für einen Weg, der zu Ihnen passt und Sie glücklich macht.</p>
    <p>Finden Sie die Mutterrolle, die es Ihnen ermöglicht, gut für sich zu sorgen und bei sich zu bleiben. Leben Sie so Ihre Bedürfnisse und Interessen im Einklang mit denen Ihrer Familie.</p>
    <h3>Beratung</h3>
    <p>Trotz einer Flut an Informationen fühlen sich viele Mütter mit ihren Themen alleine gelassen, hilflos und überfordert.</p>
    <p>Bei mir bleiben Sie nicht allein und ratlos: zusammen finden wir individuelle Antworten auf Ihre ganz persönlichen Fragen.</p>
    <div class="note">Hinweis: Es handelt sich hier um eine Beratung und nicht um eine Psychotherapie oder sonstige Heilkunde im gesetzlichen Sinne und soll diese auch nicht ersetzen.</div>
  </div>

  <div class="panel path">
    <h2>Unser Weg</h2>
    <div class="sub">Gemeinsam können wir uns Ihre Themen ansehen und bearbeiten</div>
    <div class="step"><svg viewBox="0 0 22 22"><circle cx="11" cy="11" r="10.5" fill="#7a7a7a"/><circle cx="11" cy="7" r="2" fill="#fff"/><path d="M6 15h10M8 15l3-5 3 5" stroke="#fff" stroke-width="1.4" fill="none"/></svg><span>Stressbewältigung - finden Sie den Weg zu mehr Gelassenheit, zur inneren Ruhe</span></div>
    <div class="step"><svg viewBox="0 0 22 22"><circle cx="11" cy="11" r="10.5" fill="var(--orange)"/><circle cx="11" cy="11" r="6" fill="none" stroke="#fff" stroke-width="1.4"/><path d="M11 7.5V11h3" stroke="#fff" stroke-width="1.4" fill="none"/></svg><span>Zeiteinteilung - so passen Sie Ihre Zeit der momentanen Situation an</span></div>
    <div class="step"><svg viewBox="0 0 22 22"><circle cx="11" cy="11" r="10.5" fill="#7a7a7a"/><path d="M11 5v8" stroke="#fff" stroke-width="2.4"/><circle cx="11" cy="16.5" r="1.4" fill="#fff"/></svg><span>Erhalten Sie mehr Klarheit über Ihre Bedürfnisse und Erwartungen</span></div>
    <div class="step"><svg viewBox="0 0 22 22"><circle cx="11" cy="11" r="10.5" fill="var(--orange)"/><path d="M7 5v12M11 5v12M15 5v12" stroke="#fff" stroke-width="1.2"/><rect x="5.5" y="8" width="3" height="2" fill="#fff"/><rect x="9.5" y="12" width="3" height="2" fill="#fff"/><rect x="13.5" y="9" width="3" height="2" fill="#fff"/></svg><span>Wandeln Sie Unsicherheit in Stabilität um</span></div>
    <div class="step"><svg viewBox="0 0 22 22"><circle cx="11" cy="11" r="10.5" fill="#7a7a7a"/><circle cx="11" cy="10" r="5" fill="none" stroke="#fff" stroke-width="1.4"/><path d="M9 15v2h4v-2" stroke="#fff" stroke-width="1.4" fill="none"/></svg><span>Erkennen und nutzen Sie Ihre Stärken und Fähigkeiten</span></div>
    <div class="step"><svg viewBox="0 0 22 22"><circle cx="11" cy="11" r="10.5" fill="var(--orange)"/><circle cx="8" cy="8" r="2" fill="#fff"/><circle cx="14" cy="8" r="2" fill="#fff"/><path d="M5 17v-4h6v4M11 17v-4h6v4" fill="#fff"/></svg><span>Familienberatung - so können Sie entgegenkommend miteinander umgehen</span></div>
    <div class="step"><svg viewBox="0 0 22 22"><circle cx="11" cy="11" r="10.5" fill="#7a7a7a"/><path d="M11 11L6 6M11 11L16 7M11 11L7 16M11 11L16 15" stroke="#fff" stroke-width="1.2"/><circle cx="11" cy="11" r="2" fill="#fff"/><circle cx="6" cy="6" r="1.4" fill="#fff"/><circle cx="16" cy="7" r="1.4" fill="#fff"/><circle cx="7" cy="16" r="1.4" fill="#fff"/><circle cx="16" cy="15" r="1.4" fill="#fff"/></svg><span>Netzwerk - hier finden Sie Verständnis und Unterstützung</span></div>
  </div>
</section>

<section class="spread spread--outside" aria-label="Außenseite">
  <div class="panel why">
    <div class="head">
      <h2>Warum Coaching<br>extra für Mütter?</h2>
      <p>Nur! Nur wer gut für sich selbst sorgt, kann auch für andere da sein!</p>
    </div>
    <div class="band"><h2>Coaching<br>für Mütter</h2></div>
    <div class="body">
      <p>Als Heilpraktikerin für Psychotherapie und geprüfte psychologische Beraterin habe ich mich besonders auf das Coaching für Mütter spezialisiert.</p>
      <p>Ich setzte dabei die Methode des lösungsorientierten Kurzzeitcoachings ein, das den Fokus auf Stärken und Lösungen legt und nicht die Probleme und Hindernisse in den Vordergrund stellt.</p>
      <p>Das Konzept wird durch Achtsamkeits- und Entspannungsübungen abgerundet. Aspekte der „gewaltfreien“ = wertschätzenden Kommunikation werden für individuelle Konfliktlösungen im familiären Alltag genutzt.</p>
      <p class="start">Starten Sie mit einem neuen und liebevollen Blick auf Ihr Leben und auf Ihre Fähigkeiten.</p>
    </div>
    <div class="bubble">Sie werden erstaunt sein, was alles in Ihnen wohnt.</div>
  </div>

  <div class="panel offers">
    <div class="top">
      <div class="brand">Karla Brettin</div>
      <div class="claim-line">Coaching für Mütter</div>
    </div>
    <div class="offer offer--single"><svg viewBox="0 0 20 20"><circle cx="10" cy="10" r="9.5" fill="none" stroke="#fff"/><circle cx="10" cy="7.5" r="3" fill="#fff"/><path d="M4.5 16a5.5 5 0 0 1 11 0z" fill="#fff"/></svg><h3>Einzelcoaching</h3><p>Sie können wählen: das Coaching kann in meiner Praxis in Rheinfelden oder gern auch bei Ihnen zu Hause stattfinden, allein oder mit Partner, so wie es gerade für Sie am besten passt.</p></div>
    <div class="offer offer--group"><svg viewBox="0 0 20 20"><circle cx="10" cy="10" r="9.5" fill="none" stroke="#fff"/><circle cx="7" cy="8" r="2.2" fill="#fff"/><circle cx="13" cy="8" r="2.2" fill="#fff"/><circle cx="10" cy="13" r="2.2" fill="#fff"/></svg><h3>Gruppencoaching</h3><p>Lernen Sie Gleichgesinnte kennen und profitieren Sie in doppelter Hinsicht - nach dem Motto: „Lieber gemeinsam als einsam“.</p></div>
    <div class="offer offer--phone"><svg viewBox="0 0 20 20"><circle cx="10" cy="10" r="9.5" fill="none" stroke="#fff"/><path d="M6 5.5l2.2 0 1 2.8-1.4 1a6 6 0 0 0 2.9 2.9l1-1.4 2.8 1 0 2.2c-5 .6-9.1-3.5-8.5-8.5z" fill="#fff"/></svg><h3>Telefoncoaching</h3><p>Sie bestimmen Ort und Zeit. Dieses Angebot könnte das Richtige für Sie sein, wenn Sie zeitlich oder örtlich gebunden sind.</p></div>
    <div class="contact">
      <p class="call">Rufen Sie mich doch einfach unverbindlich an.<br>Ich freue mich auf Sie!</p>
      <p class="name">Karla Brettin</p>
      <p class="role">Heilpraktikerin für Psychotherapie<br>Geprüfte Psychologische Beraterin</p>
      <p class="phone">Telefon: 0151-24608133</p>
      <p>Email: info@karla-brettin.de<br>www.karla-brettin.de</p>
      <p style="margin-top:4px">Praxisgemeinschaft am Park<br>Lindenweg 14b<br>40231 Rheinfelden</p>
    </div>
  </div>

  <div class="panel cover">
    <div class="top">
      <div class="brand">Karla Brettin</div>
      <div class="claim-line">Coaching für Mütter</div>
    </div>
    <div class="photo" role="img" aria-label="Foto: Mutter hält ihr schlafendes Neugeborenes an der Schulter"></div>
    <div class="claim">Das Baby ist da<br>und <b>nichts</b><br>ist mehr<br>wie es war!</div>
  </div>
</section>

</body>
</html>
```